I need email signatures for my admin staff members
info:
Teresa Volkaric
Support Coordinator
Unit 4, 517 Marden Vale Road, Quillby NSW 2185
Tel: 02 94637215 Mob: 0417582946
email: teresa.vo@kindwayservices.com
www.kindwayservices.com

Target Market(s)

community services industry

Industry/Entity Type

Community Service

Requirements
Must have
• Specialist Provider of Multicultural Support Services
Nice to have
• "I acknowledge the traditional owners of the land on which we live, work and dream"
plus their flags as attached

```html
<!DOCTYPE html>
<html lang="en">
<head>
<meta charset="utf-8">
<title>Kindway Services – Email Signature</title>
<link href="https://fonts.googleapis.com/css2?family=Arimo:wght@700&family=Lato:wght@400&display=swap" rel="stylesheet">
<style>
  :root {
    --backdrop: #d3d3d3;
    --card: #f7f7f7;
    --ink: #333333;
    --text: #222222;
    --orange: #f7931e;
    --charcoal: #333333;
    --rule: #555555;
    --emblem-warm: #8e2a22;
    --emblem-cool: #2c5a86;
  }
  * { margin: 0; padding: 0; box-sizing: border-box; }
  html, body {
    width: 1200px; height: 900px; overflow: hidden;
    background: var(--backdrop);
  }
  .signature {
    position: absolute; left: 72px; top: 240px;
    width: 1057px; height: 421px;
    background: var(--card);
    overflow: hidden;
  }
  .signature__corners { position: absolute; inset: 0; }
  .person {
    position: absolute; left: 88px; top: 92px;
  }
  .person__name {
    font-family: "Arimo", Arial, sans-serif; font-weight: 700;
    font-size: 50px; line-height: 60px; color: var(--ink);
  }
  .person__role {
    font-family: "Lato", sans-serif; font-weight: 400;
    font-size: 35px; line-height: 44px; color: var(--orange);
  }
  .person__accent {
    position: absolute; left: 88px; top: 220px;
    width: 55px; height: 4px; background: var(--orange);
  }
  .contact {
    position: absolute;
    font-family: "Lato", sans-serif; font-size: 22px; line-height: 28px;
    color: var(--text);
    display: flex; align-items: flex-start; gap: 7px;
  }
  .contact svg { flex: none; margin-top: 3px; }
  .contact--address { left: 72px; top: 251px; }
  .contact--tel { left: 72px; top: 320px; }
  .contact--mob { left: 72px; top: 348px; }
  .contact--email { left: 268px; top: 316px; }
  .contact--web { left: 268px; top: 346px; }
  .divider {
    position: absolute; left: 661px; top: 78px;
    width: 1px; height: 307px; background: var(--rule);
  }
  .brand {
    position: absolute; left: 680px; top: 36px; width: 332px;
    display: flex; flex-direction: column; align-items: center; gap: 10px;
  }
  .brand__dot {
    width: 104px; height: 104px; border-radius: 50%;
    background: var(--orange);
  }
  .brand__name {
    font-family: "Lato", sans-serif; font-weight: 400;
    font-size: 29px; letter-spacing: 1.5px; color: var(--orange);
    white-space: nowrap;
  }
  .acknowledgement {
    position: absolute; left: 703px; top: 225px; width: 268px;
    font-family: "Lato", sans-serif; font-size: 19px; line-height: 24.5px;
    color: var(--text);
  }
  .emblems {
    position: absolute; left: 708px; top: 312px;
    display: flex; gap: 3px;
  }
  .emblems__slot { width: 59px; height: 40px; }
  .emblems__slot--first { background: var(--emblem-warm); }
  .emblems__slot--second { background: var(--emblem-cool); }
</style>
</head>
<body>
  <section class="signature" aria-label="Email signature for Teresa Volkaric, Kindway Services">
    <svg class="signature__corners" width="1057" height="421" viewBox="0 0 1057 421" aria-hidden="true">
      <polygon points="0,0 203,0 0,105" fill="var(--orange)"/>
      <polygon points="16,20 100,78 16,118" fill="var(--charcoal)"/>
      <polygon points="754,421 1057,421 1057,265" fill="var(--charcoal)"/>
      <polygon points="938,300 1043,250 1043,375" fill="var(--orange)"/>
    </svg>

    <div class="person">
      <h1 class="person__name">Teresa Volkaric</h1>
      <p class="person__role">Support Coordinator</p>
    </div>
    <div class="person__accent"></div>

    <p class="contact contact--address">
      <svg width="24" height="24" viewBox="0 0 24 24" aria-hidden="true"><circle cx="12" cy="12" r="11" fill="none" stroke="var(--orange)" stroke-width="1.5"/><path d="M12 5.5a4 4 0 0 0-4 4c0 3 4 8 4 8s4-5 4-8a4 4 0 0 0-4-4z" fill="var(--orange)"/><circle cx="12" cy="9.5" r="1.5" fill="var(--card)"/></svg>
      <span>Unit 4, 517 Marden Vale Road,<br>Quillby NSW 2185</span>
    </p>
    <p class="contact contact--tel">
      <svg width="24" height="24" viewBox="0 0 24 24" aria-hidden="true"><circle cx="12" cy="12" r="11" fill="none" stroke="var(--orange)" stroke-width="1.5"/><path d="M8 6.5l2 0 1 3-1.3 1a7 7 0 0 0 3.8 3.8l1-1.3 3 1 0 2a1.5 1.5 0 0 1-1.7 1.4A10 10 0 0 1 6.6 8.2 1.5 1.5 0 0 1 8 6.5z" fill="var(--orange)"/></svg>
      <span>02 94637215</span>
    </p>
    <p class="contact contact--mob">
      <svg width="24" height="24" viewBox="0 0 24 24" aria-hidden="true"><circle cx="12" cy="12" r="11" fill="none" stroke="var(--orange)" stroke-width="1.5"/><rect x="8.5" y="5.5" width="7" height="13" rx="1.2" fill="var(--orange)"/><rect x="9.7" y="7" width="4.6" height="8.5" fill="var(--card)"/></svg>
      <span>0417582946</span>
    </p>
    <p class="contact contact--email">
      <svg width="24" height="24" viewBox="0 0 24 24" aria-hidden="true"><circle cx="12" cy="12" r="11" fill="none" stroke="var(--orange)" stroke-width="1.5"/><rect x="6" y="8" width="12" height="8.5" fill="var(--orange)"/><path d="M6 8l6 4.8L18 8" fill="none" stroke="var(--card)" stroke-width="1.2"/></svg>
      <span>teresa.vo@kindwayservices.com</span>
    </p>
    <p class="contact contact--web">
      <svg width="24" height="24" viewBox="0 0 24 24" aria-hidden="true"><circle cx="12" cy="12" r="11" fill="none" stroke="var(--orange)" stroke-width="1.5"/><circle cx="12" cy="12" r="6.5" fill="var(--orange)"/><path d="M5.5 12h13M12 5.5v13M7 8.5h10M7 15.5h10" stroke="var(--card)" stroke-width="0.9" fill="none"/><ellipse cx="12" cy="12" rx="3" ry="6.5" fill="none" stroke="var(--card)" stroke-width="0.9"/></svg>
      <span>www.kindwayservices.com</span>
    </p>

    <div class="divider"></div>

    <div class="brand">
      <div class="brand__dot" aria-hidden="true"></div>
      <p class="brand__name">KINDWAY SERVICES</p>
    </div>

    <p class="acknowledgement">I acknowledge the traditional owners of the land on which we live, work and dream</p>

    <div class="emblems">
      <div class="emblems__slot emblems__slot--first" role="img" aria-label="Place for the Aboriginal flag"></div>
      <div class="emblems__slot emblems__slot--second" role="img" aria-label="Place for the Torres Strait Islander flag"></div>
    </div>
  </section>
</body>
</html>
```